Corporate Business Card

Very professional, Modern, Not to busy, include phone address email, website
(253) 617-4930, 18761 52nd Avenue S, Kent, WA 98047, martin@plumlinegroup.com, varkoworks.com

Target Market(s)

Manufacturing

Industry/Entity Type

Aero, machining, manufacturing, Off road racing

Contact Information for Business Card

Phone, address email, website

```html
<!DOCTYPE html>
<html lang="en">
<head>
<meta charset="utf-8">
<title>Varko Works – Business Card</title>
<link rel="stylesheet" href="https://fonts.googleapis.com/css2?family=Exo+2:wght@700;800&family=Roboto:wght@400;500;700&display=swap">
<style>
  :root {
    --page: #2a2a2a;
    --front-top: #19191a;
    --front-bottom: #2e2e30;
    --front-mark: #4a4a4d;
    --navy-top: #2b3a6b;
    --navy-bottom: #263465;
    --red: #c9252d;
    --white: #f2f2f2;
    --ink-light: #e9ebf2;
  }
  * { box-sizing: border-box; margin: 0; padding: 0; }
  html, body { width: 1200px; height: 1138px; overflow: hidden; }
  body {
    background: var(--page);
    font-family: "Roboto", Arial, sans-serif;
    position: relative;
  }
  .card {
    position: absolute;
    width: 620px;
    height: 376px;
    border-radius: 16px;
    overflow: hidden;
  }
  /* Front side */
  .card-front {
    left: 290px;
    top: 186px;
    background: linear-gradient(160deg, var(--front-top) 0%, #1f1f20 55%, var(--front-bottom) 100%);
  }
  .front-wordmark {
    position: absolute;
    left: 0; right: 0;
    top: 118px;
    text-align: center;
    font-family: "Roboto", Arial, sans-serif;
    font-weight: 700;
    font-size: 64px;
    letter-spacing: 4px;
    color: var(--front-mark);
  }
  .front-web {
    position: absolute;
    left: 0; right: 0;
    top: 325px;
    text-align: center;
    font-size: 16px;
    letter-spacing: 11px;
    color: var(--white);
  }
  .front-web .accent { color: var(--red); }

  /* Back side */
  .card-back {
    left: 290px;
    top: 608px;
    background: linear-gradient(180deg, var(--navy-top) 0%, var(--navy-bottom) 100%);
  }
  .person-name {
    position: absolute;
    left: 34px;
    top: 45px;
    font-family: "Exo 2", "Roboto", sans-serif;
    font-weight: 800;
    font-size: 27px;
    letter-spacing: 0.5px;
    color: var(--white);
  }
  .person-name .surname { color: var(--red); }
  .contact-list {
    position: absolute;
    left: 34px;
    top: 180px;
    list-style: none;
  }
  .contact-item {
    display: flex;
    align-items: flex-start;
    font-size: 16.5px;
    line-height: 24.5px;
    color: var(--ink-light);
  }
  .contact-item svg {
    width: 16px;
    height: 16px;
    margin-top: 4px;
    margin-right: 16px;
    flex: none;
    fill: var(--red);
  }
  .contact-item .spacer { width: 32px; flex: none; }
  .brand-line {
    position: absolute;
    left: 34px;
    right: 36px;
    top: 304px;
    height: 36px;
    display: flex;
    align-items: center;
    gap: 16px;
  }
  .rule {
    flex: 1;
    height: 2px;
    background: var(--white);
  }
  .back-wordmark {
    flex: none;
    font-family: "Roboto", Arial, sans-serif;
    font-weight: 700;
    font-size: 30px;
    line-height: 36px;
    letter-spacing: 1px;
    color: var(--white);
  }
</style>
</head>
<body>

<section class="card card-front" aria-label="Card front">
  <div class="front-wordmark">VARKO WORKS</div>
  <div class="front-web">www.varko<span class="accent">works</span>.com</div>
</section>

<section class="card card-back" aria-label="Card back">
  <h1 class="person-name">MARTIN <span class="surname">HALE</span></h1>

  <ul class="contact-list">
    <li class="contact-item">
      <svg viewBox="0 0 16 16" aria-hidden="true"><path d="M8 0.5a5.5 5.5 0 0 0-5.5 5.5c0 4 5.5 9.5 5.5 9.5s5.5-5.5 5.5-9.5A5.5 5.5 0 0 0 8 0.5zm0 7.8a2.3 2.3 0 1 1 0-4.6 2.3 2.3 0 0 1 0 4.6z"/></svg>
      <span>18761 52nd Avenue S,</span>
    </li>
    <li class="contact-item"><span class="spacer"></span><span>Kent, WA 98047</span></li>
    <li class="contact-item">
      <svg viewBox="0 0 16 16" aria-hidden="true"><path d="M1 5c0-2 3-3.5 7-3.5S15 3 15 5v1.2h-3.4V4.8C10.8 4.4 9.4 4.2 8 4.2s-2.8.2-3.6.6v1.4H1z"/><path d="M3.5 7.2h9l1.5 6.8H2z"/><circle cx="8" cy="10.4" r="1.5" fill="#263465"/></svg>
      <span>(253) 617-4930</span>
    </li>
    <li class="contact-item">
      <svg viewBox="0 0 16 16" aria-hidden="true"><path d="M1 3h14v10H1z"/><path d="M1.5 3.5 8 9l6.5-5.5" fill="none" stroke="#263465" stroke-width="1.4"/></svg>
      <span>martin@plumlinegroup.com</span>
    </li>
    <li class="contact-item">
      <svg viewBox="0 0 16 16" aria-hidden="true"><g fill="none" stroke="#c9252d" stroke-width="1.3"><circle cx="8" cy="8" r="6.6"/><ellipse cx="8" cy="8" rx="3" ry="6.6"/><path d="M1.4 8h13.2M2.5 4.6h11M2.5 11.4h11"/></g></svg>
      <span>www.varkoworks.com</span>
    </li>
  </ul>

  <div class="brand-line">
    <div class="rule"></div>
    <div class="back-wordmark">VARKO WORKS</div>
  </div>
</section>

</body>
</html>
```